Poster design for "A Frame" Sign

I need a design for an A Frame sign. Measurements and Specifications here:
http://www.trimboxdepot.com.au/pg/a-boards/ABPBBLKPRT-Print-Specs.pdf

Actually, it will need to be two designs, one with an arrow pointing left and one with an arrow pointing right, otherwise exactly the same.

LOGO to be used is attached. Colours of design should match logo and should also include orange tones.

The A Frame sign is to be put on the driveway of my home studio at a main road in a residential suburban area. Cars drive by at around 50 km/h, so there needs to be an eye catcher that there is a nurturing home massage studio here.

Logo can be left or right, somehow incorporated into the text below:
-
[Big header, ideally "LeHavre" font]
Sorela Healing
Massage Studio

[slightly smaller font, serif, with bullet points]
- Relaxation Massage
- Remedial Massage
- Pregnancy Massage
- Kahuna Massage

[big Arrow to the left/right - one for each side of the frame]

[sans serif font, same size as above]
Bookings essential!
ph 0491 578 264
www.sorelahealing.com.au

[serif font, same as above]
EFTPOS and instant health fund claims available.
-

Residential

f37022

```html
<!DOCTYPE html>
<html lang="en">
<head>
<meta charset="utf-8">
<title>Sorela Healing – Massage Studio A-Frame Sign</title>
<link rel="stylesheet" href="https://fonts.googleapis.com/css2?family=Comfortaa:wght@400;700&family=Oswald:wght@300;400&family=Montserrat:wght@400&display=swap">
<style>
  :root {
    --maroon: #8b1a3c;
    --pink: #e0215f;
    --orange: #f37022;
    --yellow: #f7b52a;
    --white: #ffffff;
    --bg-light: #ffffff;
    --bg-edge: #d6d6d6;
  }
  * { margin: 0; padding: 0; box-sizing: border-box; }
  html, body { width: 810px; height: 1200px; overflow: hidden; background: var(--white); }
  .sign {
    position: relative;
    width: 810px;
    height: 1200px;
    overflow: hidden;
    background: radial-gradient(ellipse at 50% 45%, var(--bg-light) 0%, #f1f1f1 45%, var(--bg-edge) 100%);
  }
  .brand-mark {
    position: absolute;
    left: 246px;
    top: 51px;
    width: 264px;
    height: 264px;
  }
  .brand-name {
    position: absolute;
    top: 368px;
    left: 0;
    width: 100%;
    text-align: center;
    font-family: "Comfortaa", sans-serif;
    font-weight: 700;
    font-size: 60px;
    letter-spacing: 2px;
    color: var(--maroon);
    text-transform: uppercase;
  }
  .brand-rule {
    position: absolute;
    top: 451px;
    left: 264px;
    width: 278px;
    height: 2px;
    background: var(--maroon);
  }
  .studio-label {
    position: absolute;
    top: 462px;
    left: 0;
    width: 100%;
    text-align: center;
    font-family: "Oswald", sans-serif;
    font-weight: 300;
    font-size: 50px;
    letter-spacing: 15px;
    padding-left: 15px;
    color: var(--maroon);
  }
  .services {
    position: absolute;
    top: 550px;
    left: 0;
    width: 100%;
    list-style: none;
    text-align: center;
    font-family: "Comfortaa", sans-serif;
    font-size: 32px;
    line-height: 41.5px;
    color: var(--pink);
  }
  .booking-arrow {
    position: absolute;
    left: 94px;
    top: 750px;
    width: 576px;
    height: 134px;
  }
  .booking-text {
    position: absolute;
    left: 146px;
    top: 750px;
    width: 524px;
    height: 134px;
    text-align: center;
    color: var(--white);
  }
  .booking-phone {
    display: block;
    margin-top: 12px;
    font-family: "Montserrat", sans-serif;
    font-weight: 400;
    font-size: 68px;
    line-height: 72px;
    letter-spacing: 1px;
  }
  .booking-note {
    display: block;
    font-family: "Comfortaa", sans-serif;
    font-size: 25px;
    letter-spacing: 3px;
  }
  .website {
    position: absolute;
    top: 918px;
    left: 0;
    width: 100%;
    text-align: center;
    font-family: "Oswald", sans-serif;
    font-weight: 400;
    font-size: 48px;
    letter-spacing: 6px;
    color: var(--maroon);
    text-transform: uppercase;
  }
  .payment-note {
    position: absolute;
    top: 982px;
    left: 0;
    width: 100%;
    text-align: center;
    font-family: "Montserrat", sans-serif;
    font-size: 22px;
    color: var(--maroon);
  }
  .wave-bands {
    position: absolute;
    left: 0;
    top: 1000px;
    width: 810px;
    height: 200px;
  }
</style>
</head>
<body>
  <main class="sign">
    <svg class="brand-mark" viewBox="0 0 264 264" aria-hidden="true">
      <circle cx="132" cy="132" r="130" fill="var(--pink)"/>
    </svg>

    <h1 class="brand-name">Sorela Healing</h1>
    <div class="brand-rule"></div>
    <p class="studio-label">MASSAGE STUDIO</p>

    <ul class="services">
      <li>Relaxation Massage</li>
      <li>Remedial Massage</li>
      <li>Pregnancy Massage</li>
      <li>Kahuna Massage</li>
    </ul>

    <svg class="booking-arrow" viewBox="0 0 576 134" aria-hidden="true">
      <polygon points="0,67 52,0 576,0 576,134 52,134" fill="var(--pink)"/>
    </svg>
    <div class="booking-text">
      <span class="booking-phone">0491 578 264</span>
      <span class="booking-note">Bookings essential!</span>
    </div>

    <p class="website">www.sorelahealing.com.au</p>
    <p class="payment-note">EFTPOS and instant health fund claims available.</p>

    <svg class="wave-bands" viewBox="0 0 810 200" preserveAspectRatio="none" aria-hidden="true">
      <path d="M0 62 Q400 0 810 14 L810 200 L0 200 Z" fill="var(--yellow)"/>
      <path d="M0 84 Q420 30 810 50 L810 200 L0 200 Z" fill="var(--orange)"/>
      <path d="M0 110 Q380 50 810 92 L810 200 L0 200 Z" fill="var(--pink)"/>
      <path d="M0 150 Q420 92 810 138 L810 200 L0 200 Z" fill="var(--white)"/>
      <path d="M0 162 Q420 108 810 156 L810 200 L0 200 Z" fill="var(--maroon)"/>
    </svg>
  </main>
</body>
</html>
```